Custom Cabinet Shop Needs a website design

Hi,
We need a website for a Custom Cabinet Shop and Cabinet parts manufacturing business.
The business has two sides to it. One side provides custom Kitchens, vanities, entertainment units, offices and what not to homeowners and contractors.
The 2nd side of the business provides built to order cabinet boxes and other parts required to put together a project to other cabinet shops, small contractors looking to install there own cabinets.
Website will need a Gallery to display work.
Color scheme to go well with logo.
current website is www.brambleoakcustomcabinets.com
being changed to www.brambleoak.ca
Logo Included in attached files.
Tagline "Joinery with Spirit"
Mission Statement "Our passion is to deliver inspired cabinetry solutions to suit all your needs, supported by our phenomenal star class customer service"
The website should convey quality and professionalism.
Thank you.
Homeowners/ Contractors
Entertainment

```html
<!DOCTYPE html>
<html lang="en">
<head>
<meta charset="utf-8">
<title>Brambleoak Custom Cabinets</title>
<link href="https://fonts.googleapis.com/css2?family=Dosis:wght@500;600&family=Open+Sans:ital,wght@0,400;0,600;0,700;1,400&display=swap" rel="stylesheet">
<style>
  :root{
    --dark:#2a2a2a;
    --dark-2:#333;
    --accent:#e8512a;
    --quote:#d9714e;
    --ink:#333;
    --muted:#666;
    --line:#e2e2e2;
    --gray-band:#dcdcdc;
    --white:#fff;
  }
  *{margin:0;padding:0;box-sizing:border-box}
  html,body{width:801px;height:1200px;overflow:hidden}
  body{position:relative;background:var(--white);font-family:"Open Sans",Arial,sans-serif;color:var(--ink)}
  .abs{position:absolute}

  .site-header{left:0;top:0;width:801px;height:80px;background:linear-gradient(#2e2e2e,#262626)}
  .brand{left:66px;top:26px;display:flex;align-items:center;gap:7px;color:var(--white);font-family:"Dosis",sans-serif;font-weight:600;font-size:17px;letter-spacing:1px;text-transform:uppercase}
  .brand-mark{width:14px;height:14px;background:var(--accent)}
  .main-nav{right:66px;top:32px;display:flex;gap:34px}
  .main-nav a{color:var(--white);text-decoration:none;font-size:7.5px;font-weight:600;text-transform:uppercase;position:relative}
  .main-nav a.active{color:var(--accent)}
  .main-nav a.active::after{content:"";position:absolute;left:0;right:0;top:13px;height:1.5px;background:var(--accent)}

  .hero-photo{left:0;top:80px;width:801px;height:286px;background:linear-gradient(100deg,#1c2430 0%,#3a2c22 30%,#7a5436 55%,#5a4030 75%,#8a6a50 100%)}
  .hero-caption{left:242px;top:192px;width:325px;height:62px;background:rgba(255,255,255,.28);display:flex;align-items:center;justify-content:center;font-weight:700;font-size:20px;text-transform:uppercase;color:var(--white);text-shadow:0 1px 3px rgba(0,0,0,.5)}
  .hero-caption span{color:var(--accent);margin-right:6px}
  .hero-arrow{top:217px;width:10px;height:12px}

  .section-title{font-family:"Dosis",sans-serif;font-weight:500;font-size:15px;text-transform:uppercase;color:var(--ink);letter-spacing:.3px}
  .welcome-title{left:0;width:801px;top:388px;text-align:center}
  .mission{left:160px;width:481px;top:424px;text-align:center;color:var(--quote);font-size:9.5px;line-height:16px}
  .read-more{left:0;width:801px;top:466px;text-align:center;font-size:7.5px;font-style:italic;color:var(--ink)}
  .read-more i{display:inline-block;width:7px;height:7px;border-radius:50%;background:var(--ink);vertical-align:-1px;margin-left:3px}
  .divider{left:66px;top:510px;width:669px;height:1px;background:var(--line)}

  .portfolio-title{left:66px;top:536px}
  .pager{top:538px;width:15px;height:14px;border:1px solid #ddd;background:var(--white)}
  .card{left:66px;top:579px;width:669px;height:146px;background:var(--white);box-shadow:0 1px 4px rgba(0,0,0,.25);overflow:hidden}
  .card-photo{left:7px;top:8px;width:224px;height:130px;background:linear-gradient(90deg,#3a3530,#8a7060 40%,#c0b8ac 70%,#5a5048)}
  .card-sep{left:252px;top:12px;width:1px;height:122px;background:var(--line)}
  .card-title{left:272px;top:15px;font-size:9.5px;font-weight:600;text-transform:uppercase;color:var(--ink)}
  .card-point{left:272px;font-size:6.5px;text-transform:uppercase;color:var(--ink);display:flex;align-items:center;gap:6px}
  .card-point i{width:6px;height:6px;border-radius:50%;background:var(--quote)}
  .card-text{left:273px;top:92px;width:370px;font-size:7.3px;line-height:13.5px;color:var(--muted)}
  .badge{right:0;bottom:0}

  .gallery-band{left:0;top:782px;width:801px;height:364px;background:linear-gradient(135deg,#e4e4e4,#d2d2d2 50%,#e0e0e0)}
  .gallery-title{left:0;width:801px;top:803px;text-align:center}
  .thumb{width:189px;height:105px;border:3px solid var(--white);box-shadow:0 3px 5px rgba(0,0,0,.2)}

  .site-footer{left:0;top:1146px;width:801px;height:54px;background:var(--dark-2)}
  .footer-links{left:66px;top:1158px;font-size:7.5px;color:#ccc}
  .copyright{left:66px;top:1175px;font-size:7.5px;color:#ccc}
  .social{top:1163px;width:19px;height:19px;border:1px solid #777}
</style>
</head>
<body>
  <header class="site-header abs">
    <div class="brand abs"><span class="brand-mark"></span>Brambleoak</div>
    <nav class="main-nav abs">
      <a class="active" href="#">Home</a><a href="#">Gallery</a><a href="#">Services</a><a href="#">Warranty</a><a href="#">Contact</a>
    </nav>
  </header>

  <div class="hero-photo abs" role="img" aria-label="Basement bar with stone counter, bar stools and pendant lights"></div>
  <div class="hero-caption abs"><span>Joinery</span>with Spirit</div>
  <svg class="hero-arrow abs" style="left:246px" viewBox="0 0 10 12"><path d="M7 1 2 6l5 5" fill="none" stroke="#666" stroke-width="1.5"/></svg>
  <svg class="hero-arrow abs" style="left:548px" viewBox="0 0 10 12"><path d="M3 1l5 5-5 5" fill="none" stroke="#666" stroke-width="1.5"/></svg>

  <h2 class="section-title welcome-title abs">Welcome</h2>
  <p class="mission abs">“Our passion is to deliver inspired cabinetry solutions to suit all your needs, supported by our phenomenal star class customer service”</p>
  <p class="read-more abs">Read more<i></i></p>
  <div class="divider abs"></div>

  <h2 class="section-title portfolio-title abs">Portfolio</h2>
  <svg class="pager abs" style="left:703px" viewBox="0 0 15 14"><path d="M9 4 6 7l3 3" fill="none" stroke="#e8512a" stroke-width="1.4"/></svg>
  <svg class="pager abs" style="left:720px" viewBox="0 0 15 14"><path d="M6 4l3 3-3 3" fill="none" stroke="#e8512a" stroke-width="1.4"/></svg>

  <article class="card abs">
    <div class="card-photo abs" role="img" aria-label="Open kitchen with dark cabinets, island and stainless fridge"></div>
    <div class="card-sep abs"></div>
    <h3 class="card-title abs">Lorem ipsum dolor sit amet, consectetur adipiscing</h3>
    <p class="card-point abs" style="top:51px"><i></i>Vero eos et accusamus et iusto odio dignissimos</p>
    <p class="card-point abs" style="top:74px"><i></i>Vero eos et accusamus et iusto odio dignissimos</p>
    <p class="card-text abs">Lorem ipsum dolor sit amet, consectetur adipiscing elit, sed do eiusmod tempor incididunt ut labore et dolore magna aliqua. Ut enim ad minim veniam, quis nostrud exercitation ullamco laboris nisi ut aliquip ex ea commodo consequat. Duis aute irure dolor in reprehenderit</p>
    <svg class="badge abs" width="62" height="37" viewBox="0 0 62 37"><path d="M62 0V37H0Z" fill="#e8512a"/><text x="56" y="31" text-anchor="end" font-family="Georgia,serif" font-size="9" fill="#fff">NEW</text></svg>
  </article>

  <section class="gallery-band abs" aria-label="Gallery"></section>
  <h2 class="section-title gallery-title abs">Gallery</h2>
  <div class="thumb abs" style="left:58px;top:855px;background:linear-gradient(90deg,#6a6058,#b8aea4 50%,#2a2420)" role="img" aria-label="Bedroom with fireplace and tall dark cabinet"></div>
  <div class="thumb abs" style="left:292px;top:855px;background:linear-gradient(#3a3834,#1e1c1a)" role="img" aria-label="Dark stone-faced kitchen island"></div>
  <div class="thumb abs" style="left:529px;top:855px;background:linear-gradient(#2e2a28,#4a4440 60%,#aaa4a0)" role="img" aria-label="Wall of dark wood cabinets"></div>
  <div class="thumb abs" style="left:58px;top:1004px;background:linear-gradient(#d8d0c4,#3a2e28 60%,#a07850)" role="img" aria-label="Kitchen island with white panels"></div>
  <div class="thumb abs" style="left:292px;top:1004px;background:linear-gradient(#2a3040,#404858)" role="img" aria-label="Built-in shelving unit"></div>
  <div class="thumb abs" style="left:529px;top:1004px;background:linear-gradient(90deg,#5a2a20,#c8c0b4 60%,#e8e4dc)" role="img" aria-label="Kitchen with large island and red wood accent"></div>

  <footer class="site-footer abs">
  </footer>
  <p class="footer-links abs">Home &nbsp;|&nbsp; Gallery &nbsp;|&nbsp; Services &nbsp;|&nbsp; Warranty &nbsp;|&nbsp; Contact</p>
  <p class="copyright abs">Copyrights©brambleoak.2015. Allrights Reserved.</p>
  <span class="social abs" style="left:647px"></span>
  <span class="social abs" style="left:670px"></span>
  <span class="social abs" style="left:693px"></span>
  <span class="social abs" style="left:716px"></span>
</body>
</html>
```